Graphic Design Project

We make rose petal jelly from old fashioned english roses. The jelly is sweet eaten with scones and clotted cream or as a filling in a victoria sandwich, as a topping on ice cream or thick set yogurt.
The image of the product is luxurious and decadent and very english.
We need a design for a label which has a picture of an old fashioned rose (rosa mundi or a compte de chambard) The rose must stand out clearly so the jelly is not confused with other fruit jams. The overall colour of the label should be pink and soft, with white or dark pink writing. The label needs to be fridge proof.

We also need a security strip to fit on the lid of the jar.

We need the following information on the label.
Name of our company-"Meadow Crown"
Name of Product-"Rose Petal Jelly"
Sales pitch-"With whole petals-a taste of summer, delicious on scones, as a filling in sponge cake, as a topping on ice cream or yogurt."
INGREDIENTS: Sugar, water, rose petals, lemon juice, natural jelling agent (agar-agar)
STORAGE: Store in a cool dry place, once opened keep refrigerated and consume within 4 weeks.
BEST BEFORE: See base

200g
Produced by:
MEADOW CROWN
The Larches
Pardew Lane
Newnham
Gloucestershire
GL17 4RX
The label must have room for a bar code. The size of label approx 8-10cm long 5cm wide.
Updates

Hi

Just been looking at the Hartwell and Brace site and the labels they have there have the up market feel I am trying to convey. Hope that helps, its classy but not twee.

Thanks

Thanks for all submissions. I would be grateful if you googled images for 'Colourful and expensive biscuits at Hartwell Brace' The designs on the tins are the image we are trying to create. The colours are quite strong.

Thanks

Target Market(s)

older well off people who visit garden centres

Industry/Entity Type

Security

Requirements
Must have
• All writen info above and picture of old fashioned rose prferably rose a mundi. Luxury feel, very english, to appeal to older market
Pink colour sheme
Should not have
• dark or manly colours

```html
<!DOCTYPE html>
<html lang="en">
<head>
<meta charset="utf-8">
<title>Meadow Crown Rose Petal Jelly Label</title>
<link rel="stylesheet" href="https://fonts.googleapis.com/css2?family=Sorts+Mill+Goudy&display=swap">
<style>
  :root {
    --label-plum: #85074a;
    --soft-pink: #f2a8d8;
    --petal-pink: #f3b0dc;
    --paper: #ffffff;
    --ink: #1a1a1a;
    --heading-plum: #7a0a45;
    --rose-deep: #b0102a;
    --rose-bright: #e0283f;
  }
  * { margin: 0; padding: 0; box-sizing: border-box; }
  html, body {
    width: 1200px;
    height: 750px;
    overflow: hidden;
    background: var(--paper);
  }
  .label {
    position: relative;
    width: 1200px;
    height: 750px;
    font-family: "Sorts Mill Goudy", Georgia, serif;
    font-variant-numeric: oldstyle-nums;
  }
  .front-panel {
    position: absolute;
    left: 0; top: 0;
    width: 797px;
    height: 750px;
    background: var(--label-plum);
    text-align: center;
  }
  .brand-name {
    position: absolute;
    left: 0; right: 0; top: 34px;
    margin-left: 10px;
    font-size: 52px;
    font-weight: 400;
    color: var(--soft-pink);
    line-height: 1;
  }
  .product-name {
    position: absolute;
    left: 0; right: 0; top: 110px;
    margin-left: 20px;
    font-size: 72px;
    font-weight: 400;
    color: var(--paper);
    line-height: 1;
  }
  .tagline {
    position: absolute;
    left: 0; right: 0; top: 201px;
    margin-left: 20px;
    font-size: 24px;
    color: var(--petal-pink);
    line-height: 1;
  }
  .rose-cluster {
    position: absolute;
    left: 272px;
    top: 282px;
    width: 268px;
    height: 236px;
    border-radius: 46% 50% 48% 44%;
    background: radial-gradient(circle at 50% 50%, var(--rose-deep) 0%, var(--rose-bright) 60%, #e84a5e 100%);
    box-shadow: 0 0 0 4px rgba(255,255,255,0.85);
  }
  .serving-ideas {
    position: absolute;
    left: 0; right: 0; top: 578px;
    margin-left: 30px;
    font-size: 30px;
    line-height: 40px;
    color: var(--petal-pink);
  }
  .net-weight {
    position: absolute;
    left: 584px; top: 702px;
    font-size: 32px;
    color: var(--paper);
    line-height: 1;
  }
  .info-panel {
    position: absolute;
    left: 818px; top: 28px;
    width: 370px;
    color: var(--ink);
    font-size: 22px;
    line-height: 29px;
  }
  .info-heading {
    color: var(--heading-plum);
    font-weight: 400;
    font-size: 22px;
  }
  .info-block { margin-bottom: 21px; }
  .inline-heading { color: var(--heading-plum); }
  .producer {
    position: absolute;
    left: 818px; top: 380px;
    font-size: 28px;
    line-height: 35px;
    color: var(--heading-plum);
    font-style: normal;
  }
  .barcode-space {
    position: absolute;
    left: 1001px; top: 636px;
    width: 176px; height: 90px;
    border: 1.5px solid var(--ink);
    padding: 20px 0 0 7px;
    font-family: Arial, Helvetica, sans-serif;
    font-size: 18px;
    line-height: 24px;
    color: var(--ink);
  }
</style>
</head>
<body>
<main class="label">
  <section class="front-panel">
    <p class="brand-name">Meadow Crown</p>
    <h1 class="product-name">Rose Petal Jelly</h1>
    <p class="tagline">"With whole petals its a taste of summer”</p>
    <div class="rose-cluster" role="img" aria-label="Three red old fashioned roses"></div>
    <p class="serving-ideas">Delicious on scones, as a filling<br>in sponge cake, as a topping<br>on ice cream or yogurt."</p>
    <p class="net-weight">200g</p>
  </section>

  <section class="info-panel">
    <div class="info-block">
      <h2 class="info-heading">INGREDIENTS:</h2>
      <p>Sugar, water, rose petals, lemon juice, natural jelling agent (agar-agar)</p>
    </div>
    <div class="info-block">
      <p><span class="inline-heading">STORAGE:</span> Store in a cool dry place, once opened keep refrigerated and consume within 4 weeks.</p>
    </div>
    <div class="info-block">
      <h2 class="info-heading">BEST BEFORE:</h2>
      <p>See base</p>
    </div>
  </section>

  <address class="producer">
    Produced by:<br>
    MEADOW CROWN<br>
    The Larches<br>
    Pardew Lane<br>
    Newnham<br>
    Gloucestershire<br>
    GL17 4RX
  </address>

  <div class="barcode-space">Bar<br>Code</div>
</main>
</body>
</html>
```